Cruise Booking Website

Cruise search and booking website

This project is a redesign of a cruise booking website we did a few years ago.

The current website is located here: http://voyage.pylonworks.example/en/

It's not fully functional but gives you ad idea how miserable the old design was.

All the information about cruises, cruise lines, destinations, ports and shore excursions will be similar to http://www.sailquest.example/
Actual search pages (form, results, single result, sailing and cabin selection, ship info, booking) will have EXACTLY the same info as sailquest.example

We like the style of http://harborfleetdesk.example, it's quite modern, good spacing, not overloaded with information. So you can use it as an example of what we like, not what we want as a final result for us. Please, don't copy it. The result should not be possible to resemble the harborfleetdesk.example, because our site has to be unique. This is important!
If you submit a design that clearly reminds another cruise site it will be rejected!

Also the mockup provided is just to give you the basic structure and show what information has to be present on the page. It doesn't mean the layout has to be the same as a mockup. The layout is up to the designer.

I've updated the mockup to be more generic so it doesn't confuse you:
https://files.boxvault.example/s/k7m2qp9wz4hx/Home%20page.png

When you're adding social sharing icons like plazanet/chirpline you have to use chinese ones instead:
https://files.boxvault.example/s/t3nr8vx5lc2e/chinese-social-icons.png
Originals: http://minilk.example/qR7t

We'll start with home page first and after it's approved inner pages can be designed.

I know the cost of the project doesn't look high, but the task is straight forward and doesn't require to be very original, it's better to follow existing design and layout patterns that proved to work well.
That's why I encourage you to choose a template to build the design on top of one of https://themeparlor.example/ themes if it will save the design work, will be easier and faster for you. So it will be more like a customization than a new design from scratch.

Mockups, site map and logo files:
- https://files.boxvault.example/sh/h48dm2rs73fkpw/QvnbW2Xz8e

Website tree:
- https://sheets.papernest.example/document/d/7xPqR2mLw9sTk4VbN8cHj3YzA6eUf5GdKo1iMnBv/edit?usp=sharing
Updates

So far a lot of designs are just copying http://www.harborfleetdesk.example/ - we don't like it!

We like the style of harborfleetdesk.example, it's quite modern, good spacing, not overloaded with information. So you can use it as an example of what we like, not what we want as a final result for us. Please, don't copy it. The result should not be possible to resemble the harborfleetdesk.example, because our site has to be unique. This is important!

Target Market(s)

Chinese travellers

Industry/Entity Type

Build

Requirements
Must have
• * White, blue and red
* Large spacing, not too much information cramped into a small space like sailquest.example or the current website
* More "hidden" info in popups, tabs and so on, so not to many things are visible at the same time
* Compatible with kestrel scaffold styling (for easier coding):
- http://kestrelkit.codeshelf.example/scaffold/index.html
- http://skinmarket.example/
* Feel free to propose to build the design on top of one of https://themeparlor.example/ themes if it will save the design work, will be easier and faster for you

```html
<!DOCTYPE html>
<html lang="en">
<head>
<meta charset="utf-8">
<title>Haiyun Voyages – Cruise Booking</title>
<link href="https://fonts.googleapis.com/css2?family=Open+Sans:wght@400;600;700&display=swap" rel="stylesheet">
<style>
:root{
  --blue-dark:#1f5d97;
  --blue:#2c6ca8;
  --blue-light:#5fa8d3;
  --blue-pale:#9dbbd3;
  --blue-mist:#dde9f3;
  --blue-text:#2a8ac2;
  --navy-text:#1c3f66;
  --red:#d8284d;
  --red-dark:#b01a3a;
  --phone-red:#e0405f;
  --charcoal:#3a3c40;
  --panel:#d7e4ee;
  --white:#ffffff;
  --grey-text:#a8acb0;
  --ink:#222222;
}
*{box-sizing:border-box;margin:0;padding:0}
html,body{width:1200px;height:941px;overflow:hidden;background:var(--white)}
body{font-family:"Open Sans",Arial,sans-serif;color:var(--ink)}
.page{position:relative;width:1165px;height:914px;transform:scale(1.03);transform-origin:0 0;overflow:hidden}
.abs{position:absolute}

.topbar{left:0;top:0;width:1165px;height:32px;background:var(--blue-mist)}
.account-links{right:99px;top:7px;font-size:13px;color:var(--blue-text);display:flex;align-items:center;gap:10px}
.account-links .sep{color:#7aa5c8}

.header{left:0;top:32px;width:1165px;height:122px;background:var(--white)}
.brand{left:88px;top:52px;display:flex;align-items:center;gap:12px}
.brand-dot{width:70px;height:70px;border-radius:50%;background:var(--blue-dark)}
.brand-name{font-size:30px;font-weight:700;color:var(--blue-dark);letter-spacing:-.5px}
.brand-divider{left:421px;top:52px;width:1px;height:78px;background:#e2e6ea}
.tagline{left:433px;top:68px;font-size:17px;line-height:21px;color:var(--grey-text)}
.tagline em{font-style:normal;color:#6fa7d1}
.phone{right:95px;top:48px;display:flex;align-items:center;gap:10px;font-size:39px;font-weight:600;color:var(--phone-red)}
.social{right:91px;top:102px;display:flex;gap:5px}
.social span{width:24px;height:24px;border-radius:3px}

.navband{left:0;top:154px;width:1165px;height:40px;background:repeating-linear-gradient(135deg,#3274b0 0 2px,#2c6ca8 2px 5px);border-top:2px solid #4d8cc4}
.nav{left:75px;top:156px;height:38px;display:flex}
.nav a{display:block;height:37px;line-height:36px;padding:0 19px;font-size:16px;color:var(--white);text-decoration:none;border-right:1px solid #245c92}
.nav a.active{background:var(--blue-light);width:85px;text-align:center;padding:0}
.search{left:916px;top:156px;width:160px;height:37px;display:flex}
.search-field{flex:1;background:var(--white);font-size:14px;color:#444;line-height:37px;padding-left:20px}
.search-btn{width:38px;background:var(--red);display:flex;align-items:center;justify-content:center}

.band-main{left:0;top:194px;width:1165px;height:378px;background:repeating-linear-gradient(135deg,#2f6ea9 0 2px,#2a67a1 2px 5px)}
.band-lower{left:0;top:572px;width:1165px;height:60px;background:var(--blue-pale)}

.hero{left:75px;top:194px;width:703px;height:314px;background:radial-gradient(ellipse at 55% 35%,#4fb0f0 0%,#1f74c4 45%,#0b3f86 100%)}
.hero-caption{left:75px;top:423px;width:380px;height:75px;background:rgba(8,20,40,.85);color:var(--white);font-size:37px;font-weight:600;letter-spacing:-1px;line-height:75px;padding-left:29px}

.tabs{left:75px;top:508px;width:703px;height:42px;background:#a4bdd3;display:flex;gap:2px;padding-left:2px}
.tab{height:42px;line-height:44px;font-size:14px;padding:0 26px;color:#223}
.tab.on{background:var(--white);width:185px;padding-left:18px}
.tab.off{background:#c7d9e7;width:166px;border-right:2px solid var(--blue);padding-left:26px}

.content{left:75px;top:550px;width:703px;height:364px;background:var(--white)}
.card{width:224px;height:155px;border:1px solid #e3e6e9;background:repeating-linear-gradient(135deg,#f7f7f7 0 2px,#fbfbfb 2px 5px);padding:5px}
.card .photo{height:102px}
.card .caption{text-align:center;font-size:11px;line-height:17px;color:#222;padding-top:11px}
.card .caption span{border-bottom:1px solid #222}
.card .caption.two{padding-top:5px}

.finder{left:778px;top:194px;width:298px;height:340px;background:repeating-linear-gradient(135deg,#3d3f43 0 2px,#37393d 2px 5px)}
.finder h2{position:absolute;left:21px;top:17px;font-size:19px;font-weight:400;color:var(--white)}
.finder .rule{position:absolute;left:21px;top:54px;width:251px;height:1px;background:#55585c}
.select{position:absolute;left:21px;width:255px;height:34px;background:linear-gradient(#ffffff,#e7e9eb);border-radius:2px;font-size:13px;color:var(--navy-text);line-height:34px;padding-left:9px}
.select::after{content:"";position:absolute;right:34px;top:0;width:1px;height:34px;background:#c9cdd1}
.select svg{position:absolute;right:11px;top:10px}
.finder .rule2{position:absolute;left:21px;top:261px;width:251px;height:1px;background:#55585c}
.adv{position:absolute;left:16px;top:284px;font-size:12px;color:#e8e8e8;text-decoration:underline}
.btn-search{position:absolute;left:124px;top:274px;width:152px;height:42px;background:linear-gradient(#e2355a,var(--red-dark));border-radius:3px;color:var(--white);font-size:13px;line-height:42px;padding-left:13px}
.btn-search::after{content:"";position:absolute;right:34px;top:0;width:1px;height:42px;background:#a51735}
.btn-search svg{position:absolute;right:8px;top:12px}

.newsletter{left:778px;top:534px;width:298px;height:380px;background:repeating-linear-gradient(135deg,#d4e2ec 0 2px,#dbe7f0 2px 5px)}
.newsletter h3{position:absolute;left:29px;top:15px;font-size:20px;font-weight:400;color:var(--blue-text)}
.news-photo{position:absolute;left:28px;top:51px;width:238px;height:117px;background:linear-gradient(#4f8fd6 0%,#8dbbe6 55%,#2a6aa8 62%,#1d4f86 100%)}
.news-text{position:absolute;left:31px;top:181px;font-size:14px;line-height:20px;color:#222;width:220px}
.field{position:absolute;left:31px;width:239px;height:38px;background:var(--white);border:1px solid #cdd5dc;font-size:14px;font-style:italic;color:#666;line-height:36px;padding-left:13px}
.btn-sub{position:absolute;left:29px;top:327px;width:242px;height:42px;background:linear-gradient(#e2355a,var(--red-dark));border-radius:3px;color:var(--white);font-size:18px;text-align:center;line-height:42px;padding-right:30px}
.btn-sub::after{content:"";position:absolute;right:35px;top:0;width:1px;height:42px;background:#a51735}
.btn-sub svg{position:absolute;right:8px;top:11px}
</style>
</head>
<body>
<div class="page">
  <div class="abs topbar"></div>
  <div class="abs account-links">
    <svg width="12" height="12" viewBox="0 0 12 12"><path d="M1 5h6V2l4 4-4 4V7H1z" fill="#2a8ac2"/></svg>
    <span>Sign in</span><span class="sep">|</span><span>sign up</span>
  </div>

  <div class="abs header"></div>
  <div class="abs brand"><span class="brand-dot"></span><span class="brand-name">Haiyun Voyages</span></div>
  <div class="abs brand-divider"></div>
  <div class="abs tagline">China’s Most Advanced<br><em>Cruise Booking</em> Provider</div>
  <div class="abs phone">
    <svg width="30" height="30" viewBox="0 0 24 24"><path d="M6.6 10.8a15.1 15.1 0 0 0 6.6 6.6l2.2-2.2c.3-.3.7-.4 1-.2 1.1.4 2.3.6 3.6.6.6 0 1 .4 1 1V20c0 .6-.4 1-1 1A17 17 0 0 1 3 4c0-.6.4-1 1-1h3.5c.6 0 1 .4 1 1 0 1.3.2 2.5.6 3.6.1.3 0 .7-.2 1z" fill="#e0405f"/></svg>
    <span>4008 512 930</span>
  </div>
  <div class="abs social">
    <span style="background:#3a7fc9"></span><span style="background:#e8582a"></span><span style="background:#3ba6e0"></span><span style="background:#58b947"></span><span style="background:#4d8ad0"></span><span style="background:#6cc04a"></span>
  </div>

  <div class="abs navband"></div>
  <nav class="abs nav">
    <a class="active">Home</a><a>Lines</a><a>Shores</a><a>Destinations</a><a>FAQ</a><a>News</a><a>Promotions</a><a>Booking</a><a style="border-right:none">Blog</a>
  </nav>
  <div class="abs search">
    <div class="search-field">Search...</div>
    <div class="search-btn"><svg width="20" height="20" viewBox="0 0 20 20"><circle cx="11" cy="8" r="6" fill="none" stroke="#fff" stroke-width="2"/><path d="M7 12l-5 5" stroke="#fff" stroke-width="2.4"/></svg></div>
  </div>

  <div class="abs band-main"></div>
  <div class="abs band-lower"></div>

  <div class="abs hero" role="img" aria-label="Glowing blue world map on a deep blue grid"></div>
  <div class="abs hero-caption">Explore The World</div>

  <div class="abs tabs">
    <div class="tab on">Featured destinations</div>
    <div class="tab off">All destinations</div>
  </div>

  <div class="abs content"></div>
  <div class="abs card" style="left:85px;top:564px"><div class="photo" role="img" aria-label="African savanna tree at sunset" style="background:linear-gradient(#f2a51f,#d96a10 60%,#4a2608)"></div><div class="caption"><span>Africa</span></div></div>
  <div class="abs card" style="left:316px;top:564px"><div class="photo" role="img" aria-label="Alaskan mountains above green forest" style="background:linear-gradient(#6d9bd6,#a88a6a 45%,#3f6a2a)"></div><div class="caption"><span>Alaska</span></div></div>
  <div class="abs card" style="left:547px;top:564px"><div class="photo" role="img" aria-label="Ancient temple carved into rock cliffs" style="background:linear-gradient(#b48a6c,#8a5c40 60%,#c7a184)"></div><div class="caption"><span>Asia-Pacific &amp; the Middle East</span></div></div>

  <div class="abs card" style="left:85px;top:726px"><div class="photo" role="img" aria-label="City skyline with tower and harbour sailboats" style="background:linear-gradient(#cfe0ef,#8fa6bb 55%,#5c6f82)"></div><div class="caption two"><span>Australia &amp; New Zealand</span><br><span>Australia &amp; New Zealand Cruise Tours</span></div></div>
  <div class="abs card" style="left:316px;top:726px"><div class="photo" role="img" aria-label="Turquoise bay with a coastal town" style="background:linear-gradient(#1e8fd0,#2aa6c8 55%,#b89a6a)"></div><div class="caption"><span>Bahamas</span></div></div>
  <div class="abs card" style="left:547px;top:726px"><div class="photo" role="img" aria-label="White sand beach with rocks and clear water" style="background:linear-gradient(#9fd3e8,#6fc5d3 45%,#e9e3d6)"></div><div class="caption"><span>Bermuda</span></div></div>

  <div class="abs card" style="left:85px;top:888px"><div class="photo" role="img" aria-label="Destination view under a blue sky" style="background:linear-gradient(#2f6bb8,#4b86c9)"></div></div>
  <div class="abs card" style="left:316px;top:888px"><div class="photo" role="img" aria-label="Tropical palms under a bright sky" style="background:linear-gradient(#5aa9e6,#9fcfee)"></div></div>
  <div class="abs card" style="left:547px;top:888px"><div class="photo" role="img" aria-label="Palm fronds against a pale sky" style="background:linear-gradient(#8ab6d9,#5c8a5a)"></div></div>

  <div class="abs finder">
    <h2>Find Your Cruise</h2>
    <div class="rule"></div>
    <div class="select" style="top:71px">Popular Destinations<svg width="10" height="14" viewBox="0 0 10 14"><path d="M5 0l5 5H0zM5 14L0 9h10z" fill="#555"/></svg></div>
    <div class="select" style="top:118px">Any Length<svg width="10" height="14" viewBox="0 0 10 14"><path d="M5 0l5 5H0zM5 14L0 9h10z" fill="#555"/></svg></div>
    <div class="select" style="top:164px">Any Length<svg width="10" height="14" viewBox="0 0 10 14"><path d="M5 0l5 5H0zM5 14L0 9h10z" fill="#555"/></svg></div>
    <div class="select" style="top:210px;padding-left:12px">Any Cruise Line<svg width="10" height="14" viewBox="0 0 10 14"><path d="M5 0l5 5H0zM5 14L0 9h10z" fill="#555"/></svg></div>
    <div class="rule2"></div>
    <div class="adv">Advanced Search</div>
    <div class="btn-search">Search Cruises<svg width="18" height="18" viewBox="0 0 20 20"><circle cx="11" cy="8" r="6" fill="none" stroke="#fff" stroke-width="2"/><path d="M7 12l-5 5" stroke="#fff" stroke-width="2.4"/></svg></div>
  </div>

  <div class="abs newsletter">
    <h3>Cruise Deals Newsletter</h3>
    <div class="news-photo" role="img" aria-label="Large white cruise ship at sea"></div>
    <p class="news-text">Subscribe an recive the beals cruise deals now!</p>
    <div class="field" style="top:233px">Name</div>
    <div class="field" style="top:279px">Email</div>
    <div class="btn-sub">Subscribe<svg width="20" height="20" viewBox="0 0 20 20"><circle cx="10" cy="10" r="8.5" fill="none" stroke="#fff" stroke-width="1.6"/><path d="M5 10h9M10 6l4 4-4 4" fill="none" stroke="#fff" stroke-width="1.6"/></svg></div>
  </div>
</div>
</body>
</html>
```